Harborview Optical -Window Poster (Optometrist)

We are an optometry practice and we need a poster for a new store promotion for our window highlighting we now also sell 2 pairs of glasses as a package deal. The size will be 1300mm width x 1900mm height

The artwork will be displayed as a fabric banner in our shop window. We have 7 other banners with different services our business provides. The words needs to standout for passers by and the cars stopped at the traffic lights out front of our business. We already have signs with our logos phone number etc. so we won't need them included in the poster.

It would need to include the following information.

Two pair packages now available*

*Conditions apply

The artwork will be displayed as a fabric banner in our shop window. We have 7 other banners with different services our business provides. The words needs to standout for passers by and the cars stopped at the traffic lights out front of our business. We already have signs with our logos phone number etc. so we won't need them included in the poster. Thank you for your work it's amazing Added Saturday, February 18, 2017

The artwork will be displayed as a fabric banner in our shop window. We have 7 other banners with different services our business provides. The words needs to standout for passers by and the cars stopped at the traffic lights out front of our business. We already have signs with our logos phone number etc. so we won't need them included in the poster. Added Saturday, February 18, 2017

Target Market(s)

Cars driving past and stopped at traffic lights outside our store.

Industry/Entity Type

Optician

Requirements
Must have
• Poster must say:
• Two pair packages now available*
• *Conditions apply

```html
<!DOCTYPE html>
<html lang="en">
<head>
<meta charset="utf-8">
<title>Two Pair Packages – Window Poster</title>
<link rel="stylesheet" href="https://fonts.googleapis.com/css2?family=Archivo+Black&family=Oswald:wght@700&display=swap">
<style>
  :root {
    --poster-top: #262422;
    --poster-mid: #4a443e;
    --poster-low: #2c2926;
    --headline: #f4f4f2;
    --accent-red: #df2226;
    --accent-red-light: #ea3a2e;
    --offer-yellow: #fff21a;
    --sticker-face: #e9e9e7;
    --sticker-shade: #bdbdbb;
    --sticker-ink: #141414;
  }
  * { margin: 0; padding: 0; box-sizing: border-box; }
  html, body { width: 962px; height: 1200px; overflow: hidden; background: var(--poster-top); }
  .poster {
    position: relative;
    width: 962px;
    height: 1200px;
    overflow: hidden;
    background: radial-gradient(ellipse 70% 55% at 50% 60%, var(--poster-mid) 0%, var(--poster-low) 70%, var(--poster-top) 100%);
  }
  .skyline {
    position: absolute;
    left: 0; right: 0; bottom: 0;
    height: 290px;
    background: linear-gradient(to bottom, rgba(30,28,26,0) 0%, #2a2724 18%, #27241f 60%, #2d2a26 100%);
  }
  .top-bar {
    position: absolute;
    left: 127px; top: 153px;
    width: 704px; height: 54px;
    background: linear-gradient(90deg, var(--accent-red-light), var(--accent-red));
  }
  .headline {
    position: absolute;
    left: 0; right: 0;
    text-align: center;
    white-space: nowrap;
    font-family: "Archivo Black", "Arial Black", sans-serif;
    color: var(--headline);
    text-shadow: 0 6px 14px rgba(0,0,0,0.55);
    line-height: 1;
  }
  .headline--count { top: 232px; font-size: 258px; letter-spacing: -2px; }
  .headline--word { top: 497px; font-size: 148px; letter-spacing: -1px; }
  .offer-band {
    position: absolute;
    left: 74px; top: 784px;
    width: 787px; height: 135px;
    background: var(--accent-red);
    display: flex;
    align-items: center;
    padding-left: 33px;
  }
  .offer-text {
    font-family: "Oswald", "Impact", sans-serif;
    font-weight: 700;
    font-size: 68px;
    letter-spacing: 4px;
    color: var(--offer-yellow);
    line-height: 1;
  }
  .sticker {
    position: absolute;
    left: 688px; top: 696px;
    width: 250px; height: 250px;
  }
  .sticker-text {
    font-family: "Archivo Black", "Arial Black", sans-serif;
    font-size: 25px;
    fill: var(--sticker-ink);
  }
</style>
</head>
<body>
<main class="poster">
  <div class="skyline" role="img" aria-label="Faint dusk photograph of a city skyline across the lower part of the poster"></div>

  <div class="top-bar"></div>

  <h1 class="headline headline--count">2 PAIR</h1>
  <p class="headline headline--word">PACKAGES</p>

  <div class="offer-band">
    <span class="offer-text">NOW AVAILABLE*</span>
  </div>

  <svg class="sticker" viewBox="0 0 250 250" aria-label="Conditions apply sticker">
    <defs>
      <radialGradient id="stickerFace" cx="40%" cy="45%" r="65%">
        <stop offset="0%" stop-color="#f7f7f5"/>
        <stop offset="75%" stop-color="#e6e6e4"/>
        <stop offset="100%" stop-color="#c9c9c7"/>
      </radialGradient>
      <linearGradient id="stickerCurl" x1="0" y1="0" x2="0" y2="1">
        <stop offset="0%" stop-color="#ffffff"/>
        <stop offset="100%" stop-color="#a9a9a7"/>
      </linearGradient>
    </defs>
    <path d="M20 80 Q60 52 130 58 Q200 62 238 92 Q252 150 220 200 Q175 248 110 240 Q45 228 18 170 Q6 120 20 80 Z"
          fill="url(#stickerFace)" stroke="#9d9d9b" stroke-width="1.5"/>
    <path d="M20 80 Q30 30 90 18 Q170 8 232 42 Q248 60 238 92 Q200 62 130 58 Q60 52 20 80 Z"
          fill="url(#stickerCurl)" stroke="#9d9d9b" stroke-width="1.5"/>
    <g transform="rotate(10 125 140)">
      <text class="sticker-text" x="125" y="132" text-anchor="middle">*CONDITIONS</text>
      <text class="sticker-text" x="125" y="160" text-anchor="middle">APPLY</text>
    </g>
  </svg>
</main>
</body>
</html>
```